Redesign a Start-Up Dating Website

Website: https://morvelique.com.
Make sure the design has an island style theme.
I would like the 7 pages of my website to have a new and professional look. I want the same colors to remain, but I want a creative look for all the pages. This is a dating website that is in the startup stage. So, I want to give my entire website a custom makeover. I want something that will stand out from the other dating sites. Something that will attract more people to want to use my services, and hopefully get new members.
Target Market(s)
Dating
Industry/Entity Type
Dating
Coding
Coded - Design and coding required
Number of Pages Required
5+ page
Font styles to use
Other font styles liked:
- Decorative, San Serif
Requirements
Must have
- The design must have the original colors and a stylish font to go along. The design must be creative, welcoming, and professional. I would like an island style theme for the website. This is a dating website so make sure that the design is tailored to that aspect.
Nice to have
- It would be nice to have a decorative font and a professional style on all the pages. Make sure the design will be mobile responsive and friendly for all the pages on the website.
Should not have
- The design should not be bland and uncreative.

```html
<!DOCTYPE html>
<html lang="en">
<head>
<meta charset="utf-8">
<title>Morvelique – Find Your Perfect Match</title>
<link href="https://fonts.googleapis.com/css2?family=Lato:wght@300;400;700;900&display=swap" rel="stylesheet">
<style>
:root{
  --orange:#f7941d;
  --orange-light:#fbb03b;
  --orange-pale:#fde3bf;
  --purple:#7a4a9e;
  --teal:#3fbfae;
  --ink:#3c3c46;
  --muted:#8a8a94;
  --grey-bg:#f1f1f3;
  --white:#ffffff;
}
*{box-sizing:border-box;margin:0;padding:0}
html,body{width:1200px;height:2780px;overflow:hidden}
body{font-family:'Lato',sans-serif;color:var(--ink);background:var(--white);position:relative}
.page{width:1200px;height:2780px;position:relative;overflow:hidden}

/* Header */
.site-header{height:112px;position:relative;background:var(--white)}
.account-links{position:absolute;top:0;right:60px;display:flex;gap:6px}
.account-links a{display:block;padding:6px 18px;font-size:13px;font-weight:700;color:var(--white);text-decoration:none}
.btn-signup{background:var(--purple)}
.btn-login{background:var(--orange)}
.brand{position:absolute;left:120px;top:36px;display:flex;align-items:center;gap:12px}
.brand-dot{width:46px;height:46px;border-radius:50%;background:var(--orange)}
.brand-name{font-size:40px;font-weight:900;color:var(--orange);letter-spacing:.5px}
.main-nav{position:absolute;right:100px;top:58px;display:flex;gap:30px}
.main-nav a{font-size:16px;color:var(--ink);text-decoration:none}
.main-nav a.active{color:var(--teal)}

/* Hero */
.hero{height:528px;position:relative;background:linear-gradient(100deg,#6b5a52 0%,#a88a72 35%,#c7a78a 60%,#8f7564 100%)}
.hero-photo{position:absolute;inset:0}
.hero-copy{position:absolute;left:120px;top:245px;color:var(--white)}
.hero-copy .lead{font-size:38px;font-weight:300}
.hero-copy h1{font-size:46px;font-weight:700;line-height:1.2}
.search-panel{position:absolute;left:740px;top:48px;width:320px;height:440px;background:rgba(122,74,158,.88);padding:34px 26px}
.search-panel label{display:block;color:var(--white);font-size:14px;margin:14px 0 6px}
.search-panel label:first-child{margin-top:0}
.field{height:36px;background:var(--white);border-radius:3px;display:flex;align-items:center;justify-content:space-between;padding:0 12px;font-size:13px;color:var(--muted)}
.field svg{width:10px;height:10px}
.field-row{display:flex;gap:10px}
.field-row .field{flex:1}
.field-country{margin-top:18px}
.btn-search{margin-top:22px;height:42px;background:var(--teal);color:var(--white);font-weight:700;font-size:15px;letter-spacing:1px;display:flex;align-items:center;justify-content:center;border-radius:3px}
.hero-dots{position:absolute;bottom:14px;left:0;right:0;display:flex;justify-content:center;gap:8px}
.hero-dots span{width:12px;height:12px;border-radius:50%;background:rgba(255,255,255,.55)}
.hero-dots span.on{background:var(--white)}

/* How it works */
.how{height:380px;position:relative;text-align:center;padding-top:72px}
.section-title{font-size:34px;font-weight:700;color:var(--purple)}
.steps{display:flex;justify-content:center;gap:130px;margin-top:50px}
.step{width:220px}
.step-icon{width:96px;height:96px;margin:0 auto;border-radius:50%;background:radial-gradient(circle at 50% 40%,var(--orange-pale) 0%,var(--orange-light) 100%)}
.step h3{font-size:19px;font-weight:700;color:var(--purple);margin-top:16px}
.step p{font-size:12px;color:var(--muted);margin-top:8px;line-height:1.5}

/* Orange band */
.promo{height:500px;position:relative;color:var(--white);text-align:center}
.promo-bg{position:absolute;inset:0}
.promo-inner{position:relative;padding-top:120px}
.promo h2{font-size:40px;font-weight:700}
.promo .sub{font-size:18px;margin-top:14px;line-height:1.5}
.promo .body{font-size:13px;width:720px;margin:26px auto 0;line-height:1.7;opacity:.95}
.btn-outline{display:inline-block;margin-top:40px;padding:14px 30px;border:2px solid var(--white);font-size:15px;font-weight:700}

/* Members */
.members{height:440px;text-align:center;padding-top:58px;position:relative}
.member-row{display:flex;justify-content:center;gap:28px;margin-top:36px}
.member{width:168px}
.member-photo{height:180px;background:linear-gradient(160deg,#d8c4b2,#9c8473)}
.member-name{font-size:14px;margin-top:10px}
.member-meta{font-size:12px;color:var(--teal);margin-top:4px}
.arrow{position:absolute;top:280px;width:16px;height:28px}
.arrow-left{left:100px}
.arrow-right{right:100px}

/* Feature cards */
.features{height:360px;background:var(--grey-bg);display:flex;justify-content:center;gap:60px;padding-top:80px}
.card{width:440px;height:240px;background:var(--white);border-radius:10px;box-shadow:0 8px 24px rgba(0,0,0,.1);display:flex;gap:22px;padding:28px}
.card-photo{flex:none;width:160px;height:184px;border-radius:8px;background:linear-gradient(150deg,#e7b8a4,#9a6e5c)}
.card-text{flex:1;min-width:0}
.card h3{font-size:26px;font-weight:700;color:var(--orange);line-height:1.2}
.card p{font-size:12px;color:var(--muted);line-height:1.6;margin-top:12px}
.card .more{font-size:12px;font-weight:700;color:var(--purple);margin-top:22px;display:block}

/* Footer */
.site-footer{height:460px;position:relative;background:linear-gradient(90deg,#4cc3ab 0%,#4ea9bd 45%,#6d74b4 75%,#7c5aa6 100%);color:var(--white)}
.footer-badge{position:absolute;left:560px;top:12px;width:80px;height:80px;border-radius:50%;background:var(--white);display:flex;align-items:center;justify-content:center}
.footer-badge span{width:50px;height:50px;border-radius:50%;background:var(--orange)}
.footer-cols{position:absolute;top:130px;left:110px;display:flex}
.footer-col{width:240px}
.footer-col h4{font-size:20px;font-weight:400;margin-bottom:18px}
.footer-col li{list-style:none;font-size:13px;line-height:1.9;opacity:.9}
.contact-line{display:flex;align-items:center;gap:8px;font-size:12px;line-height:1.7;margin-bottom:8px}
.contact-line svg{width:14px;height:14px;flex:none}
.signup{display:flex}
.signup .input{width:130px;height:36px;border:1px solid var(--white);font-size:12px;padding:10px;opacity:.9}
.signup .submit{height:36px;background:var(--orange);padding:0 20px;font-size:13px;font-weight:700;display:flex;align-items:center}
.socials{display:flex;gap:10px;margin-top:18px}
.socials span{width:26px;height:26px;border-radius:50%;border:2px solid var(--white)}
.copyright{position:absolute;bottom:0;left:0;right:0;height:50px;background:rgba(0,0,0,.08);text-align:center;font-size:12px;line-height:50px;opacity:.9}
</style>
</head>
<body>
<div class="page">

<header class="site-header">
  <div class="account-links">
    <a class="btn-signup" href="#">Sign Up</a>
    <a class="btn-login" href="#">Log In</a>
  </div>
  <div class="brand"><span class="brand-dot"></span><span class="brand-name">Morvelique</span></div>
  <nav class="main-nav">
    <a class="active" href="#">Home</a><a href="#">Search</a><a href="#">Members</a><a href="#">Extras</a><a href="#">About</a><a href="#">Premium</a><a href="#">Contact</a>
  </nav>
</header>

<section class="hero">
  <div class="hero-photo" role="img" aria-label="Photo of a smiling couple embracing outdoors in warm sunlight"></div>
  <div class="hero-copy">
    <p class="lead">Let's Find Your</p>
    <h1>Perfect Match Today</h1>
  </div>
  <form class="search-panel">
    <label>I am</label>
    <div class="field">Man<svg viewBox="0 0 10 10"><path d="M1 3l4 4 4-4" fill="none" stroke="#8a8a94" stroke-width="1.5"/></svg></div>
    <label>Seeking a</label>
    <div class="field">Woman<svg viewBox="0 0 10 10"><path d="M1 3l4 4 4-4" fill="none" stroke="#8a8a94" stroke-width="1.5"/></svg></div>
    <label>Age</label>
    <div class="field-row">
      <div class="field">18<svg viewBox="0 0 10 10"><path d="M1 3l4 4 4-4" fill="none" stroke="#8a8a94" stroke-width="1.5"/></svg></div>
      <div class="field">25<svg viewBox="0 0 10 10"><path d="M1 3l4 4 4-4" fill="none" stroke="#8a8a94" stroke-width="1.5"/></svg></div>
    </div>
    <div class="field field-country">Select Country<svg viewBox="0 0 10 10"><path d="M1 3l4 4 4-4" fill="none" stroke="#8a8a94" stroke-width="1.5"/></svg></div>
    <div class="btn-search">SEARCH</div>
  </form>
  <div class="hero-dots"><span></span><span class="on"></span><span></span><span></span></div>
</section>

<section class="how">
  <h2 class="section-title">How it Works</h2>
  <div class="steps">
    <div class="step">
      <div class="step-icon" role="img" aria-label="Illustrated icon for creating a profile"></div>
      <h3>Create a Profile</h3>
      <p>Tell us who you are, add a few details and photos so the right people can find you.</p>
    </div>
    <div class="step">
      <div class="step-icon" role="img" aria-label="Illustrated icon for finding matches"></div>
      <h3>Find Matches</h3>
      <p>Browse other members and let our matching help you meet people who share your interests.</p>
    </div>
    <div class="step">
      <div class="step-icon" role="img" aria-label="Illustrated icon for starting to date"></div>
      <h3>Start Dating</h3>
      <p>Send a message, plan a first date and start a story on the island of romance today.</p>
    </div>
  </div>
</section>

<section class="promo">
  <svg class="promo-bg" viewBox="0 0 1200 500" preserveAspectRatio="none" aria-hidden="true">
    <defs><linearGradient id="orangeBand" x1="0" y1="0" x2="0" y2="1"><stop offset="0" stop-color="#fbb03b"/><stop offset="1" stop-color="#f7941d"/></linearGradient></defs>
    <path d="M0 40C300 100 500 0 800 30S1100 80 1200 20V500H0z" fill="#fde3bf"/>
    <path d="M0 70C300 120 550 20 850 60S1100 90 1200 50V500H0z" fill="url(#orangeBand)"/>
  </svg>
  <div class="promo-inner">
    <h2>Dating is Easy with Morvelique</h2>
    <p class="sub">Sign up for a 30 days free trial<br>Enjoy all the benefits Morvelique has to offer with a full membership.</p>
    <p class="body">Join a friendly community of singles looking for real connection. Create your profile in minutes, browse members near you, chat freely and discover someone who shares your love of sun, sea and adventure. Your island romance starts with one simple step.</p>
    <span class="btn-outline">Get Started Now</span>
  </div>
</section>

<section class="members">
  <h2 class="section-title">Our Members</h2>
  <svg class="arrow arrow-left" viewBox="0 0 16 28"><path d="M14 2L3 14l11 12" fill="none" stroke="#bbb" stroke-width="3"/></svg>
  <svg class="arrow arrow-right" viewBox="0 0 16 28"><path d="M2 2l11 12L2 26" fill="none" stroke="#bbb" stroke-width="3"/></svg>
  <div class="member-row">
    <div class="member"><div class="member-photo" role="img" aria-label="Member portrait photo"></div><p class="member-name">Member Name</p><p class="member-meta">Age 30, City Area</p></div>
    <div class="member"><div class="member-photo" role="img" aria-label="Member portrait photo"></div><p class="member-name">Member Name</p><p class="member-meta">Age 28, City Area</p></div>
    <div class="member"><div class="member-photo" role="img" aria-label="Member portrait photo"></div><p class="member-name">Member Name</p><p class="member-meta">Age 26, City Area</p></div>
    <div class="member"><div class="member-photo" role="img" aria-label="Member portrait photo"></div><p class="member-name">Member Name</p><p class="member-meta">Age 32, City Area</p></div>
    <div class="member"><div class="member-photo" role="img" aria-label="Member portrait photo"></div><p class="member-name">Member Name</p><p class="member-meta">Age 27, City Area</p></div>
  </div>
</section>

<section class="features">
  <article class="card">
    <div class="card-photo" role="img" aria-label="Photo of a happy couple holding a heart"></div>
    <div class="card-text">
      <h3>Success Stories</h3>
      <p>Read how our members met, fell in love and began their own island romance together.</p>
      <span class="more">READ MORE ›</span>
    </div>
  </article>
  <article class="card">
    <div class="card-photo" role="img" aria-label="Photo of a smiling couple outdoors"></div>
    <div class="card-text">
      <h3>Feature Benefits</h3>
      <p>Discover the extra tools that premium members enjoy to find a match faster and easier.</p>
      <span class="more">READ MORE ›</span>
    </div>
  </article>
</section>

<footer class="site-footer">
  <div class="footer-badge"><span></span></div>
  <div class="footer-cols">
    <div class="footer-col">
      <h4>Quick Links</h4>
      <ul><li>Explore</li><li>About</li><li>Contact</li><li>Login</li><li>Testimonials</li></ul>
    </div>
    <div class="footer-col">
      <h4>Resources</h4>
      <ul><li>Members</li><li>Premium</li><li>Register</li><li>Search</li></ul>
    </div>
    <div class="footer-col">
      <h4>Contact Us</h4>
      <p class="contact-line"><svg viewBox="0 0 14 14"><path d="M7 1a4 4 0 014 4c0 3-4 8-4 8S3 8 3 5a4 4 0 014-4z" fill="#fff"/></svg>48 Palm Harbor Road, Suite 200<br>Coral Bay 00000</p>
      <p class="contact-line"><svg viewBox="0 0 14 14"><path d="M3 1l3 3-2 2c1 2 2 3 4 4l2-2 3 3-2 2C6 13 1 8 1 3z" fill="#fff"/></svg>555-010-0199</p>
      <p class="contact-line"><svg viewBox="0 0 14 14"><rect x="1" y="3" width="12" height="8" fill="none" stroke="#fff" stroke-width="1.5"/><path d="M1 3l6 5 6-5" fill="none" stroke="#fff" stroke-width="1.5"/></svg>hello@morvelique.com</p>
    </div>
    <div class="footer-col">
      <h4>Email Sign Up</h4>
      <div class="signup"><div class="input">Email address</div><div class="submit">Subscribe</div></div>
      <div class="socials"><span></span><span></span><span></span><span></span></div>
    </div>
  </div>
  <p class="copyright">© 2017 Morvelique. All rights reserved. Terms of Use</p>
</footer>

</div>
</body>
</html>
```